UI/ UX Design for ERP Software

We need a new UX/UI interface for a ERP software for property managers. Our CMMS / ERP solution is made based on responsive design technologies and is coded in PHP.
The overall UX to be similar to Tev Ulna - easy navigation, intuitive menus.

Industry/Entity Type

Property Management

Number of Pages Required

5+ page

Requirements
Must have
• Round dock buttons
Consistent icons across the application
Enough Spacing between buttons/icons/ menu
Consistent Font
Nice to have
• We would like the UX to allow the users to use the application without /minimum training.
Should not have
• we don't want anything that is classic with respect to UX

```html
<!DOCTYPE html>
<html lang="en">
<head>
<meta charset="utf-8">
<title>Domora — Property Manager Dashboard</title>
<link href="https://fonts.googleapis.com/css2?family=Inter:wght@400;500;600;700&display=swap" rel="stylesheet">
<style>
:root{
  --page-top:#ffffff;
  --page-bottom:#e9edf2;
  --accent:#0ab4fd;
  --ink:#1b1f2a;
  --light-panel:#f3f8fc;
  --light-tile:#ffffff;
  --light-label:#8b939e;
  --dark-panel:#242938;
  --dark-tile:#333a4b;
  --dark-label:#ffffff;
  --stat-card:#ffffff;
  --stat-sub:#8b939e;
  --moon-bg:#1e2433;
  --chip-light:#e6ecf3;
  --chip-dark:#2f3646;
  --sun:#f6b800;
}
*{box-sizing:border-box;margin:0;padding:0}
html,body{width:1200px;height:1200px;overflow:hidden}
body{
  font-family:'Inter',Arial,sans-serif;
  background:linear-gradient(180deg,var(--page-top) 0%,#eef1f4 45%,var(--page-bottom) 70%,#f2f5f8 100%);
  position:relative;
}
.theme-label{
  position:absolute;left:143px;
  font-size:14px;font-weight:700;color:var(--ink);
  transform:translate(-50%,-50%) rotate(-90deg);
  white-space:nowrap;
}
.panel{
  position:absolute;left:206px;width:788px;height:478px;border-radius:26px;
  --tile:var(--light-tile);--label:var(--light-label);--text:var(--ink);--chip:var(--chip-light);
  background:var(--panel);color:var(--text);
  box-shadow:0 18px 40px rgba(40,55,80,.08);
}
.panel.light{top:88px;--panel:var(--light-panel)}
.panel.dark{top:623px;--panel:var(--dark-panel);--tile:var(--dark-tile);--label:var(--dark-label);--text:#ffffff;--chip:var(--chip-dark)}
.topbar{position:absolute;left:27px;right:25px;top:16px;height:25px;display:flex;align-items:center}
.refresh{width:25px;height:25px;border-radius:6px;background:var(--tile);display:flex;align-items:center;justify-content:center;color:var(--text)}
.brand{margin-left:15px;display:flex;align-items:center;gap:4px;font-size:9.5px;font-weight:600}
.brand-mark{width:9px;height:9px;border:1.4px solid currentColor;border-radius:2px}
.toolbar{margin-left:auto;display:flex;gap:13.5px}
.round-btn{width:25px;height:25px;border-radius:50%;background:var(--chip);display:flex;align-items:center;justify-content:center;color:var(--text)}
.round-btn.moon{background:var(--moon-bg);color:#fff}
.round-btn.sun{color:var(--sun)}
.welcome{position:absolute;left:27px;top:55px;font-size:12.5px;font-weight:400}
.welcome b{font-weight:600}
.dock{position:absolute;left:28px;top:82px;display:grid;grid-template-columns:repeat(10,48px);column-gap:27.5px;row-gap:26px}
.dock-item{display:flex;flex-direction:column;align-items:center;width:48px}
.tile{width:48px;height:48px;border-radius:10px;background:var(--tile);display:flex;align-items:center;justify-content:center;color:var(--text)}
.dock-item.active .tile{background:var(--accent);color:#fff}
.dock-label{margin-top:8px;font-size:7.4px;color:var(--label);white-space:nowrap;font-weight:500}
.ico{width:18px;height:18px;fill:none;stroke:currentColor;stroke-width:1.5;stroke-linecap:round;stroke-linejoin:round}
.ico.sm{width:11px;height:11px}
.section-title{position:absolute;top:245px;font-size:10.5px;font-weight:600}
.latest-title{left:27px}
.see-all{position:absolute;left:440px;top:247px;font-size:8px;font-weight:600}
.stats-title{left:503px}
.cards{position:absolute;left:27px;top:277px;display:grid;grid-template-columns:repeat(4,96px);column-gap:18.6px}
.photo{width:96px;height:125px;border-radius:9px}
.photo.tower{background:linear-gradient(160deg,#1d4fa8 0%,#123069 45%,#1a1f2e 80%,#3a2c25 100%)}
.photo.pool{background:linear-gradient(180deg,#9fb4d6 0%,#c9d3e0 35%,#6f747c 55%,#35b6df 75%,#b9bcc0 100%)}
.photo.apartments{background:linear-gradient(180deg,#3d6fc4 0%,#e8ecef 30%,#d7dadd 55%,#4c88c6 78%,#d9dcdf 100%)}
.photo.house{background:linear-gradient(180deg,#eef1f3 0%,#7a7f6b 30%,#5a5a40 50%,#4d8a2e 75%,#7cae3e 100%)}
.card-name{margin-top:9px;margin-left:1px;font-size:8px;font-weight:600}
.card-addr{margin-top:5px;display:flex;gap:4px;font-size:7.3px;line-height:1.3}
.card-addr .ico{width:9px;height:9px;margin-top:3px;flex:none}
.stats{position:absolute;left:502px;top:272px;display:grid;grid-template-columns:127px 127px;column-gap:6px;row-gap:5px}
.stat{height:43.5px;border-radius:5px;background:var(--stat-card);display:flex;align-items:center;padding-left:11px;gap:7px;color:var(--ink)}
.stat .ico{width:17px;height:17px;stroke-width:1.3}
.stat-name{font-size:7.3px;font-weight:600}
.stat-value{font-size:7.3px;color:var(--stat-sub);margin-top:2px}
</style>
</head>
<body>

<svg width="0" height="0" style="position:absolute" aria-hidden="true">
  <defs>
    <symbol id="i-home" viewBox="0 0 24 24"><path d="M4 11l8-7 8 7v9h-5v-5h-6v5H4z"/></symbol>
    <symbol id="i-customers" viewBox="0 0 24 24"><circle cx="12" cy="8" r="4"/><path d="M5 20c0-4 3-6 7-6s7 2 7 6z"/></symbol>
    <symbol id="i-properties" viewBox="0 0 24 24"><path d="M4 20V4h10v16M14 9h6v11M3 20h18M7 8h4M7 11h4M7 14h4M16 12h2M16 15h2"/></symbol>
    <symbol id="i-tenants" viewBox="0 0 24 24"><path d="M3 11l9-7 9 7M5 9.5V20h14V9.5"/><circle cx="12" cy="12" r="2"/><path d="M9 17c0-2 1.5-3 3-3s3 1 3 3z"/></symbol>
    <symbol id="i-contacts" viewBox="0 0 24 24"><path d="M6 4l3 1 1 4-2 1.5c1 2.5 3 4.5 5.5 5.5L15 14l4 1 1 3-2 2C10 20 4 14 4 6z"/><path d="M14 4a6 6 0 0 1 6 6M14 7.5a3 3 0 0 1 2.5 2.5"/></symbol>
    <symbol id="i-contractors" viewBox="0 0 24 24"><circle cx="12" cy="5" r="1.8"/><path d="M12 7v4M5 11h14v3H5zM6 14v6h12v-6"/></symbol>
    <symbol id="i-maintenance" viewBox="0 0 24 24"><path d="M14 4a4 4 0 0 0-4 5L4 15l3 3 6-6a4 4 0 0 0 5-4l-2 2-2-2 2-2a4 4 0 0 0-2-2z"/><path d="M14 14l5 5"/></symbol>
    <symbol id="i-works" viewBox="0 0 24 24"><rect x="4" y="5" width="16" height="15" rx="2"/><path d="M9 5V3h6v2M8 16a4 4 0 0 1 8 0"/><circle cx="12" cy="11" r="1"/></symbol>
    <symbol id="i-purchase" viewBox="0 0 24 24"><rect x="5" y="5" width="14" height="16" rx="2"/><path d="M9 5V3h6v2M14 10h-3a1.5 1.5 0 0 0 0 3h2a1.5 1.5 0 0 1 0 3h-3M12 8.5v9"/></symbol>
    <symbol id="i-requests" viewBox="0 0 24 24"><path d="M9 5h12v11h-6l-3 3v-3H9zM3 7h4M2 10h5M4 13h3M15 8v4M15 14.5v.1"/></symbol>
    <symbol id="i-analytics" viewBox="0 0 24 24"><path d="M4 20h16M6 20v-5M10 20v-7M14 20v-6M18 20v-9M5 12l5-4 3 3 6-6M15 5h4v4"/></symbol>
    <symbol id="i-config" viewBox="0 0 24 24"><path d="M3 6h18M3 12h18M3 18h18"/><circle cx="8" cy="6" r="2"/><circle cx="16" cy="12" r="2"/><circle cx="9" cy="18" r="2"/></symbol>
    <symbol id="i-settings" viewBox="0 0 24 24"><circle cx="12" cy="12" r="3"/><circle cx="12" cy="12" r="7.5" stroke-dasharray="3 1.7"/></symbol>
    <symbol id="i-inspections" viewBox="0 0 24 24"><circle cx="10.5" cy="10.5" r="6" stroke-width="2"/><path d="M15 15l5 5" stroke-width="2"/></symbol>
    <symbol id="i-energy" viewBox="0 0 24 24"><path d="M13 4h6v6h-6zM15 4V2M17 4V2M16 10v3a4 4 0 0 1-4 4H9M5 15h4v5H5zM3 16.5h2M3 18.5h2"/></symbol>
    <symbol id="i-compliance" viewBox="0 0 24 24"><circle cx="12" cy="12" r="2.5"/><circle cx="12" cy="4" r="1.5"/><circle cx="12" cy="20" r="1.5"/><circle cx="5" cy="8" r="1.5"/><circle cx="19" cy="8" r="1.5"/><circle cx="5" cy="16" r="1.5"/><circle cx="19" cy="16" r="1.5"/><path d="M12 5.5v4M12 14.5v4M6.3 8.8l3.5 2M17.7 8.8l-3.5 2M6.3 15.2l3.5-2M17.7 15.2l-3.5-2"/></symbol>
    <symbol id="i-risk" viewBox="0 0 24 24"><path d="M12 3l10 18H2z"/><path d="M12 10v5M12 17.5v.1"/></symbol>
    <symbol id="i-budget" viewBox="0 0 24 24"><circle cx="12" cy="12" r="8.5" stroke-dasharray="2 2"/><path d="M14.5 9h-3a1.5 1.5 0 0 0 0 3h1a1.5 1.5 0 0 1 0 3h-3M12 7v10"/></symbol>
    <symbol id="i-project" viewBox="0 0 24 24"><circle cx="12" cy="5" r="2"/><circle cx="6" cy="15" r="2"/><circle cx="18" cy="15" r="2"/><path d="M9 10c0-1.5 1.5-2.5 3-2.5s3 1 3 2.5M3 20c0-2 1.5-3 3-3s3 1 3 3M15 20c0-2 1.5-3 3-3s3 1 3 3M9 20h6M8 13l2-3M16 13l-2-3"/></symbol>
    <symbol id="i-reports" viewBox="0 0 24 24"><path d="M6 3h9l4 4v14H6z"/><path d="M9 17v-3M12 17v-5M15 17v-2"/></symbol>
    <symbol id="i-pin" viewBox="0 0 24 24"><path d="M12 21s-7-6.5-7-11.5a7 7 0 0 1 14 0C19 14.5 12 21 12 21z"/><circle cx="12" cy="9.5" r="2.5"/></symbol>
    <symbol id="i-area" viewBox="0 0 24 24"><path d="M11 3v15M11 3h6v5h-6M11 18H7v-4M4 21h10v-3"/></symbol>
    <symbol id="i-refresh" viewBox="0 0 24 24"><path d="M18 12a6 6 0 1 1-3-5.2M15 3v4h4"/></symbol>
    <symbol id="i-moon" viewBox="0 0 24 24"><path d="M15 4a8 8 0 1 0 5 11 6.5 6.5 0 0 1-5-11z" fill="currentColor"/></symbol>
    <symbol id="i-sun" viewBox="0 0 24 24"><circle cx="12" cy="12" r="4"/><path d="M12 2v2M12 20v2M2 12h2M20 12h2M5 5l1.5 1.5M17.5 17.5L19 19M5 19l1.5-1.5M17.5 6.5L19 5"/></symbol>
    <symbol id="i-sort" viewBox="0 0 24 24"><path d="M5 7h14M5 12h10M5 17h6" stroke-width="2.2"/></symbol>
    <symbol id="i-expand" viewBox="0 0 24 24"><path d="M4 4l5 5M4 4v4M4 4h4M20 4l-5 5M20 4v4M20 4h-4M4 20l5-5M4 20v-4M4 20h4M20 20l-5-5M20 20v-4M20 20h-4"/></symbol>
    <symbol id="i-logout" viewBox="0 0 24 24"><path d="M12 4h6a2 2 0 0 1 2 2v12a2 2 0 0 1-2 2h-6M4 12h11M8 8l-4 4 4 4"/></symbol>
  </defs>
</svg>

<div class="theme-label" style="top:333px">Light theme</div>
<div class="theme-label" style="top:857px">Dark theme</div>

<!-- Light theme panel -->
<section class="panel light">
  <header class="topbar">
    <div class="refresh"><svg class="ico sm"><use href="#i-refresh"/></svg></div>
    <div class="brand"><span class="brand-mark"></span>Domora</div>
    <div class="toolbar">
      <div class="round-btn moon"><svg class="ico sm"><use href="#i-moon"/></svg></div>
      <div class="round-btn"><svg class="ico sm"><use href="#i-sort"/></svg></div>
      <div class="round-btn"><svg class="ico sm"><use href="#i-expand"/></svg></div>
      <div class="round-btn"><svg class="ico sm"><use href="#i-logout"/></svg></div>
    </div>
  </header>
  <h1 class="welcome">Welcome, <b>Rafe Kellan</b></h1>
  <nav class="dock">
    <div class="dock-item active"><div class="tile"><svg class="ico"><use href="#i-home"/></svg></div><span class="dock-label">Home</span></div>
    <div class="dock-item"><div class="tile"><svg class="ico"><use href="#i-customers"/></svg></div><span class="dock-label">Customers</span></div>
    <div class="dock-item"><div class="tile"><svg class="ico"><use href="#i-properties"/></svg></div><span class="dock-label">Properties</span></div>
    <div class="dock-item"><div class="tile"><svg class="ico"><use href="#i-tenants"/></svg></div><span class="dock-label">Tenants</span></div>
    <div class="dock-item"><div class="tile"><svg class="ico"><use href="#i-contacts"/></svg></div><span class="dock-label">Contacts</span></div>
    <div class="dock-item"><div class="tile"><svg class="ico"><use href="#i-contractors"/></svg></div><span class="dock-label">Contractors</span></div>
    <div class="dock-item"><div class="tile"><svg class="ico"><use href="#i-maintenance"/></svg></div><span class="dock-label">Maintenance</span></div>
    <div class="dock-item"><div class="tile"><svg class="ico"><use href="#i-works"/></svg></div><span class="dock-label">Works orders</span></div>
    <div class="dock-item"><div class="tile"><svg class="ico"><use href="#i-purchase"/></svg></div><span class="dock-label">Purchase orders</span></div>
    <div class="dock-item"><div class="tile"><svg class="ico"><use href="#i-requests"/></svg></div><span class="dock-label">Tenant requests</span></div>
    <div class="dock-item"><div class="tile"><svg class="ico"><use href="#i-analytics"/></svg></div><span class="dock-label">Analytics</span></div>
    <div class="dock-item"><div class="tile"><svg class="ico"><use href="#i-config"/></svg></div><span class="dock-label">Configuration</span></div>
    <div class="dock-item"><div class="tile"><svg class="ico"><use href="#i-settings"/></svg></div><span class="dock-label">Settings</span></div>
    <div class="dock-item"><div class="tile"><svg class="ico"><use href="#i-inspections"/></svg></div><span class="dock-label">Inspections</span></div>
    <div class="dock-item"><div class="tile"><svg class="ico"><use href="#i-energy"/></svg></div><span class="dock-label">Energy</span></div>
    <div class="dock-item"><div class="tile"><svg class="ico"><use href="#i-compliance"/></svg></div><span class="dock-label">Compliance</span></div>
    <div class="dock-item"><div class="tile"><svg class="ico"><use href="#i-risk"/></svg></div><span class="dock-label">Risk mngmt</span></div>
    <div class="dock-item"><div class="tile"><svg class="ico"><use href="#i-budget"/></svg></div><span class="dock-label">Budgeting</span></div>
    <div class="dock-item"><div class="tile"><svg class="ico"><use href="#i-project"/></svg></div><span class="dock-label">Project mngmt</span></div>
    <div class="dock-item"><div class="tile"><svg class="ico"><use href="#i-reports"/></svg></div><span class="dock-label">Reports</span></div>
  </nav>
  <h2 class="section-title latest-title">Latest properties added</h2>
  <a class="see-all">See all</a>
  <div class="cards">
    <article><div class="photo tower" role="img" aria-label="Photo of a glass office tower at dusk"></div><h3 class="card-name">Prime tower</h3><p class="card-addr"><svg class="ico"><use href="#i-pin"/></svg><span>42 Harbourline Road,<br>Port Elm, BC</span></p></article>
    <article><div class="photo pool" role="img" aria-label="Photo of a residential complex with a swimming pool"></div><h3 class="card-name">Prime tower</h3><p class="card-addr"><svg class="ico"><use href="#i-pin"/></svg><span>42 Harbourline Road,<br>Port Elm, BC</span></p></article>
    <article><div class="photo apartments" role="img" aria-label="Photo of a white apartment block behind a pool"></div><h3 class="card-name">Prime tower</h3><p class="card-addr"><svg class="ico"><use href="#i-pin"/></svg><span>42 Harbourline Road,<br>Port Elm, BC</span></p></article>
    <article><div class="photo house" role="img" aria-label="Photo of a detached house with a garden path"></div><h3 class="card-name">Prime tower</h3><p class="card-addr"><svg class="ico"><use href="#i-pin"/></svg><span>42 Harbourline Road,<br>Port Elm, BC</span></p></article>
  </div>
  <h2 class="section-title stats-title">Stadistics</h2>
  <div class="stats">
    <div class="stat"><svg class="ico"><use href="#i-area"/></svg><div><div class="stat-name">Total properties areas</div><div class="stat-value">422,000.00 sq.ft.</div></div></div>
    <div class="stat"><svg class="ico"><use href="#i-area"/></svg><div><div class="stat-name">Rented area</div><div class="stat-value">233,500.00 sq.ft.</div></div></div>
    <div class="stat"><svg class="ico"><use href="#i-tenants"/></svg><div><div class="stat-name">Tenants</div><div class="stat-value">8</div></div></div>
    <div class="stat"><svg class="ico"><use href="#i-properties"/></svg><div><div class="stat-name">Properties</div><div class="stat-value">3</div></div></div>
    <div class="stat"><svg class="ico"><use href="#i-area"/></svg><div><div class="stat-name">Vacancies area</div><div class="stat-value">188,500.00 sq.ft.</div></div></div>
  </div>
</section>

<!-- Dark theme panel -->
<section class="panel dark">
  <header class="topbar">
    <div class="refresh"><svg class="ico sm"><use href="#i-refresh"/></svg></div>
    <div class="brand"><span class="brand-mark"></span>Domora</div>
    <div class="toolbar">
      <div class="round-btn sun"><svg class="ico sm"><use href="#i-sun"/></svg></div>
      <div class="round-btn"><svg class="ico sm"><use href="#i-sort"/></svg></div>
      <div class="round-btn"><svg class="ico sm"><use href="#i-expand"/></svg></div>
      <div class="round-btn"><svg class="ico sm"><use href="#i-logout"/></svg></div>
    </div>
  </header>
  <h1 class="welcome">Welcome, <b>Rafe Kellan</b></h1>
  <nav class="dock">
    <div class="dock-item active"><div class="tile"><svg class="ico"><use href="#i-home"/></svg></div><span class="dock-label">Home</span></div>
    <div class="dock-item"><div class="tile"><svg class="ico"><use href="#i-customers"/></svg></div><span class="dock-label">Customers</span></div>
    <div class="dock-item"><div class="tile"><svg class="ico"><use href="#i-properties"/></svg></div><span class="dock-label">Properties</span></div>
    <div class="dock-item"><div class="tile"><svg class="ico"><use href="#i-tenants"/></svg></div><span class="dock-label">Tenants</span></div>
    <div class="dock-item"><div class="tile"><svg class="ico"><use href="#i-contacts"/></svg></div><span class="dock-label">Contacts</span></div>
    <div class="dock-item"><div class="tile"><svg class="ico"><use href="#i-contractors"/></svg></div><span class="dock-label">Contractors</span></div>
    <div class="dock-item"><div class="tile"><svg class="ico"><use href="#i-maintenance"/></svg></div><span class="dock-label">Maintenance</span></div>
    <div class="dock-item"><div class="tile"><svg class="ico"><use href="#i-works"/></svg></div><span class="dock-label">Works orders</span></div>
    <div class="dock-item"><div class="tile"><svg class="ico"><use href="#i-purchase"/></svg></div><span class="dock-label">Purchase orders</span></div>
    <div class="dock-item"><div class="tile"><svg class="ico"><use href="#i-requests"/></svg></div><span class="dock-label">Tenant requests</span></div>
    <div class="dock-item"><div class="tile"><svg class="ico"><use href="#i-analytics"/></svg></div><span class="dock-label">Analytics</span></div>
    <div class="dock-item"><div class="tile"><svg class="ico"><use href="#i-config"/></svg></div><span class="dock-label">Configuration</span></div>
    <div class="dock-item"><div class="tile"><svg class="ico"><use href="#i-settings"/></svg></div><span class="dock-label">Settings</span></div>
    <div class="dock-item"><div class="tile"><svg class="ico"><use href="#i-inspections"/></svg></div><span class="dock-label">Inspections</span></div>
    <div class="dock-item"><div class="tile"><svg class="ico"><use href="#i-energy"/></svg></div><span class="dock-label">Energy</span></div>
    <div class="dock-item"><div class="tile"><svg class="ico"><use href="#i-compliance"/></svg></div><span class="dock-label">Compliance</span></div>
    <div class="dock-item"><div class="tile"><svg class="ico"><use href="#i-risk"/></svg></div><span class="dock-label">Risk mngmt</span></div>
    <div class="dock-item"><div class="tile"><svg class="ico"><use href="#i-budget"/></svg></div><span class="dock-label">Budgeting</span></div>
    <div class="dock-item"><div class="tile"><svg class="ico"><use href="#i-project"/></svg></div><span class="dock-label">Project mngmt</span></div>
    <div class="dock-item"><div class="tile"><svg class="ico"><use href="#i-reports"/></svg></div><span class="dock-label">Reports</span></div>
  </nav>
  <h2 class="section-title latest-title">Latest properties added</h2>
  <a class="see-all">See all</a>
  <div class="cards">
    <article><div class="photo tower" role="img" aria-label="Photo of a glass office tower at dusk"></div><h3 class="card-name">Prime tower</h3><p class="card-addr"><svg class="ico"><use href="#i-pin"/></svg><span>42 Harbourline Road,<br>Port Elm, BC</span></p></article>
    <article><div class="photo pool" role="img" aria-label="Photo of a residential complex with a swimming pool"></div><h3 class="card-name">Prime tower</h3><p class="card-addr"><svg class="ico"><use href="#i-pin"/></svg><span>42 Harbourline Road,<br>Port Elm, BC</span></p></article>
    <article><div class="photo apartments" role="img" aria-label="Photo of a white apartment block behind a pool"></div><h3 class="card-name">Prime tower</h3><p class="card-addr"><svg class="ico"><use href="#i-pin"/></svg><span>42 Harbourline Road,<br>Port Elm, BC</span></p></article>
    <article><div class="photo house" role="img" aria-label="Photo of a detached house with a garden path"></div><h3 class="card-name">Prime tower</h3><p class="card-addr"><svg class="ico"><use href="#i-pin"/></svg><span>42 Harbourline Road,<br>Port Elm, BC</span></p></article>
  </div>
  <h2 class="section-title stats-title">Stadistics</h2>
  <div class="stats">
    <div class="stat"><svg class="ico"><use href="#i-area"/></svg><div><div class="stat-name">Total properties areas</div><div class="stat-value">422,000.00 sq.ft.</div></div></div>
    <div class="stat"><svg class="ico"><use href="#i-area"/></svg><div><div class="stat-name">Rented area</div><div class="stat-value">233,500.00 sq.ft.</div></div></div>
    <div class="stat"><svg class="ico"><use href="#i-tenants"/></svg><div><div class="stat-name">Tenants</div><div class="stat-value">8</div></div></div>
    <div class="stat"><svg class="ico"><use href="#i-properties"/></svg><div><div class="stat-name">Properties</div><div class="stat-value">3</div></div></div>
    <div class="stat"><svg class="ico"><use href="#i-area"/></svg><div><div class="stat-name">Vacancies area</div><div class="stat-value">188,500.00 sq.ft.</div></div></div>
  </div>
</section>

</body>
</html>
```